Trade Show - double sided 4m wide graphic wall

I am attending a trade show where I am speaking on behalf of my former company. As part of the deal a 'stand space' is provided and all we are asked for is to provide the graphics in file format for the show organisers to produce.The stand had display boards of 4 x 1m wide and about 2.6m high. The wall has a small wraparound end graphic and then more panels on the revers so images are needed for both sides. A detail of the panel set-up is attached to this brief.The session I will be talking at is too small/medium e-commerce sellers who use Tradelo and Vendora as their main storefronts as well as their own websites. the company I'm representing are a fulfilment house. They hold their client's products in their warehouse and then receive orders from the clients end customers. My company then processes the orders, picks and packs the product and sends it out to the end consumer....in effect handles the whole warehousing and back end aspect. I wish this graphic to display our company branding and then have a theme or approach that holds this together with images that show the capabilities of the facilities we have available, as well as our capability to integrate with Vendora, Tradelo and other online stores. there will also be a few bullet points to integrate. I have attached details of the display panels I need. The specification is that they need to be 300dpi CMYK PDF's with 3mm bleed and offset crop marks (High res PDF file). I can supply you with a short video that shows you very quickly the type of thing we undertake that I hope may give you a feel for the business and I have a number of images and logos I can supply but would need to provide them via a dropbox link as there are too many and the sizes are too great to add to this request.I am coming to this requirement very late, so need to get a solution in place ASAP.

Target Market(s)

Trade Show Audience - Potential customers

Font styles to use
Sans Serif

Colors
85acd3
3377b5
33a6d7
32a6d6
ffffff

Requirements
Must have
• my company branding and images although others you may have access to and are related are fine.
Nice to have
• thoughts thus far are a collage or abstract backgroud image with more focused images in front but your the expert!

```html
<!DOCTYPE html>
<html lang="en">
<head>
<meta charset="utf-8">
<title>Dash Fulfilment – Trade Show Wall</title>
<link href="https://fonts.googleapis.com/css2?family=Ubuntu:wght@400;500;700&display=swap" rel="stylesheet">
<style>
  :root {
    --navy: #243f6e;
    --navy-deep: #1c3260;
    --accent: #3a67b5;
    --white: #ffffff;
    --logo-ink: #2a3f8f;
    --icon-ink: #243f6e;
  }
  * { margin: 0; padding: 0; box-sizing: border-box; }
  html, body { width: 1200px; height: 604px; overflow: hidden; background: var(--white); }
  body { font-family: "Ubuntu", sans-serif; }
  .wall { position: relative; width: 1200px; height: 604px; background: var(--white); }
  .wall-frame { position: absolute; left: 6px; top: 6px; width: 1189px; height: 592px; background: var(--navy); }
  .trim { position: absolute; left: 6px; width: 1189px; height: 6px; background: var(--white); }
  .trim--top { top: 18px; }
  .trim--bottom { top: 578px; }
  .end-panel { position: absolute; top: 24px; width: 100px; height: 554px; background: var(--navy); }
  .end-panel--left { left: 6px; }
  .end-panel--right { left: 1095px; border-left: 1px solid var(--navy-deep); }
  .end-url {
    position: absolute; left: 50%; top: 50%;
    transform: translate(-50%, -50%) rotate(-90deg);
    color: var(--white); font-size: 29px; font-weight: 500; white-space: nowrap;
  }
  .hero { position: absolute; left: 106px; top: 24px; width: 989px; height: 554px; }
  .hero svg { display: block; }
  .headline {
    position: absolute; left: 106px; top: 179px; width: 989px;
    text-align: center; color: var(--white); font-weight: 500;
    font-size: 23.5px; line-height: 36px; text-transform: uppercase;
    text-shadow: 2px 0 0 var(--navy-deep), -2px 0 0 var(--navy-deep), 0 2px 0 var(--navy-deep),
                 0 -2px 0 var(--navy-deep), 2px 2px 0 var(--navy-deep), -2px -2px 0 var(--navy-deep),
                 2px -2px 0 var(--navy-deep), -2px 2px 0 var(--navy-deep), 0 0 6px var(--navy-deep);
  }
  .brand {
    position: absolute; left: 832px; top: 36px; width: 232px; height: 99px;
    background: var(--white); display: flex; align-items: center; justify-content: center; gap: 12px;
  }
  .brand-dot { width: 42px; height: 42px; border-radius: 50%; background: var(--logo-ink); }
  .brand-name { color: var(--logo-ink); font-weight: 500; font-size: 27px; line-height: 1.05; }
  .services {
    position: absolute; left: 198px; top: 442px; width: 804px; height: 80px;
    border: 2px solid var(--accent); border-radius: 16px;
  }
  .service { position: absolute; display: flex; align-items: center; gap: 6px;
    color: var(--white); font-size: 10px; font-weight: 500; letter-spacing: .25px;
    text-transform: uppercase; white-space: nowrap; }
  .service-icon { width: 26px; height: 26px; border-radius: 50%; background: var(--white); flex: none;
    display: flex; align-items: center; justify-content: center; box-shadow: 0 0 0 1.5px #c9d3e6 inset; }
  .service-icon svg { width: 15px; height: 15px; fill: none; stroke: var(--icon-ink); stroke-width: 1.3;
    stroke-linecap: round; stroke-linejoin: round; }
  .site-pill {
    position: absolute; left: 458px; top: 534px; width: 285px; height: 31px;
    background: var(--accent); border-radius: 14px; color: var(--white);
    display: flex; align-items: center; justify-content: center; gap: 7px;
    font-size: 22px; font-weight: 500;
  }
  .site-pill svg { flex: none; }
</style>
</head>
<body>
<main class="wall">
  <div class="wall-frame"></div>
  <div class="trim trim--top"></div>
  <div class="trim trim--bottom"></div>

  <aside class="end-panel end-panel--left"><span class="end-url">www.dashfulfilment.com</span></aside>

  <section class="hero">
    <svg width="989" height="554" viewBox="0 0 989 554">
      <defs>
        <linearGradient id="aisle-warm" x1="0" y1="0" x2="1" y2="0">
          <stop offset="0" stop-color="#f1cf8a"/>
          <stop offset=".45" stop-color="#d59a4c"/>
          <stop offset="1" stop-color="#7a4a1e"/>
        </linearGradient>
        <linearGradient id="aisle-cool" x1="0" y1="0" x2="1" y2="0">
          <stop offset="0" stop-color="#3b3f63"/>
          <stop offset=".4" stop-color="#6b6a80"/>
          <stop offset=".7" stop-color="#4a4f78"/>
          <stop offset="1" stop-color="#9c8a73"/>
        </linearGradient>
        <radialGradient id="aisle-glow" cx=".5" cy=".6" r=".5">
          <stop offset="0" stop-color="#f3c680" stop-opacity=".55"/>
          <stop offset="1" stop-color="#f3c680" stop-opacity="0"/>
        </radialGradient>
      </defs>
      <g role="img" aria-label="Warehouse aisles with racking stacked with boxed and pallet-wrapped stock">
        <rect width="360" height="430" fill="url(#aisle-warm)"/>
        <rect x="360" width="629" height="430" fill="url(#aisle-cool)"/>
        <ellipse cx="870" cy="240" rx="160" ry="170" fill="url(#aisle-glow)"/>
        <ellipse cx="680" cy="330" rx="120" ry="110" fill="url(#aisle-glow)"/>
      </g>
      <path d="M0 412 C120 370 250 320 360 310 C520 300 600 390 760 395 C880 398 950 360 989 340 L989 554 L0 554 Z" fill="var(--accent)"/>
      <path d="M0 430 C130 380 260 338 370 328 C520 318 610 405 770 410 C890 412 955 378 989 360 L989 554 L0 554 Z" fill="var(--navy)"/>
    </svg>
  </section>

  <div class="brand">
    <span class="brand-dot"></span>
    <span class="brand-name">Dash<br>Fulfilment</span>
  </div>

  <h1 class="headline">When it comes to logistics solutions,<br>we understand each business has<br>different needs</h1>

  <section class="services">
    <div class="service" style="left:21px;top:6px"><span class="service-icon"><svg viewBox="0 0 16 16"><circle cx="8" cy="6" r="4"/><path d="M4 10v2a4 2 0 0 0 8 0v-2"/></svg></span>Cosmetics Logistics Services</div>
    <div class="service" style="left:226px;top:6px"><span class="service-icon"><svg viewBox="0 0 16 16"><path d="M6 1v3l-2 4 2 7h4l2-7-2-4V1"/></svg></span>Fashion Retail Logistics</div>
    <div class="service" style="left:408px;top:6px"><span class="service-icon"><svg viewBox="0 0 16 16"><rect x="4" y="2" width="9" height="12" rx="1"/><path d="M2 4v10h2"/></svg></span>Marketing Materials Distribution</div>
    <div class="service" style="left:655px;top:6px"><span class="service-icon"><svg viewBox="0 0 16 16"><rect x="2" y="4" width="12" height="10" rx="1"/><path d="M6 4V2h4v2M4 8h5M4 11h3"/></svg></span>Travel Logistics</div>
    <div class="service" style="left:25px;top:39px"><span class="service-icon"><svg viewBox="0 0 16 16"><rect x="2" y="5" width="12" height="9" rx="1"/><path d="M4 5l7-3 1 3M10 10h4"/></svg></span>Financial Services Logistics</div>
    <div class="service" style="left:231px;top:39px"><span class="service-icon"><svg viewBox="0 0 16 16"><path d="M2 14V6l3-3h6l3 3v8zM6 14v-4h4v4"/></svg></span>Retail Logistics</div>
    <div class="service" style="left:368px;top:39px"><span class="service-icon"><svg viewBox="0 0 16 16"><rect x="2" y="3" width="12" height="8" rx="1"/><path d="M5 14h6M8 11v3M4 6h5M4 8h7"/></svg></span>Information Technology</div>
    <div class="service" style="left:566px;top:39px"><span class="service-icon"><svg viewBox="0 0 16 16"><path d="M4 9a3 3 0 0 1 1-6 3 3 0 0 1 6 0 3 3 0 0 1 1 6v5H4z"/></svg></span>Online Food Logistics Services</div>
  </section>

  <div class="site-pill">
    <svg width="17" height="17" viewBox="0 0 16 16" aria-hidden="true"><circle cx="9.5" cy="6.5" r="5" fill="none" stroke="#fff" stroke-width="1.2"/><path d="M4.5 6.5h10M9.5 1.5v10M5.5 9 1 14" fill="none" stroke="#fff" stroke-width="1.2"/></svg>
    www.dashfulfilment.com
  </div>

  <aside class="end-panel end-panel--right"><span class="end-url">www.dashfulfilment.com</span></aside>
</main>
</body>
</html>
```